Visit card

Industry/Entity Type

Health Care

Contact Information for Business Card

O VITALIS SYSTEMS
Odile Brevard - chef de Projet

Requirements
Must have
• 318 Gaston Lemaire Street 59710 VALMERON Tel: 33 (0) 327 481 605 Mobile: 06 42 19 37 64 Web: www.quorvexsystems.example Contact: o.brevard@o-vitalissystems.example
Should not have
• Respect for color

```html
<!DOCTYPE html>
<html lang="fr">
<head>
<meta charset="utf-8">
<title>O Vitalis Systems – Carte de visite</title>
<link rel="stylesheet" href="https://fonts.googleapis.com/css2?family=Lato:wght@400;700&display=swap">
<style>
  :root {
    --stage: #2a2a2b;
    --card: #ffffff;
    --card-shade: #ececec;
    --brand-red: #e11f2b;
    --ink: #333335;
    --ink-soft: #55575a;
    --rule: #4a4a4c;
    --ghost: #f0f0f1;
  }
  * { margin: 0; padding: 0; box-sizing: border-box; }
  html, body {
    width: 1200px; height: 900px; overflow: hidden;
    background: var(--stage);
    font-family: "Lato", sans-serif;
  }
  .card {
    position: absolute; left: 75px; top: 150px;
    width: 1050px; height: 600px;
    border-radius: 34px;
    background: linear-gradient(160deg, var(--card-shade) 0%, var(--card) 45%, var(--card) 100%);
    overflow: hidden;
    color: var(--ink);
  }
  .card__ghost-disc {
    position: absolute; left: 590px; top: 110px;
    width: 400px; height: 400px;
    border-radius: 50%;
    background: var(--ghost);
  }
  .brand {
    position: absolute; left: 60px; top: 52px;
    display: flex; align-items: center; gap: 22px;
  }
  .brand__dot {
    width: 76px; height: 76px; border-radius: 50%;
    background: var(--brand-red);
  }
  .brand__name {
    font-weight: 700; font-size: 40px; letter-spacing: 1px;
    color: var(--brand-red);
  }
  .card__rule {
    position: absolute; left: 60px; right: 50px; top: 300px;
    height: 2px; background: var(--rule);
  }
  .contact {
    position: absolute; left: 60px; top: 330px;
    list-style: none;
    font-size: 21px; color: var(--ink-soft);
  }
  .contact__item {
    display: flex; align-items: center; gap: 14px;
    height: 36px;
  }
  .contact__icon { width: 16px; height: 16px; flex: none; }
  .person {
    position: absolute; right: 50px; top: 244px;
    text-align: right;
  }
  .person__name {
    font-size: 42px; font-weight: 400; letter-spacing: 0.5px;
    color: var(--brand-red); text-transform: uppercase;
    line-height: 50px;
  }
  .person__role {
    margin-top: 14px;
    font-size: 24px; color: var(--ink-soft);
  }
  .address {
    position: absolute; right: 90px; bottom: 60px;
    font-style: normal; text-align: right;
    font-size: 24px; line-height: 36px; color: var(--ink);
  }
</style>
</head>
<body>
  <article class="card">
    <div class="card__ghost-disc" aria-hidden="true"></div>

    <header class="brand">
      <span class="brand__dot" aria-hidden="true"></span>
      <span class="brand__name">O VITALIS SYSTEMS</span>
    </header>

    <div class="card__rule"></div>

    <section class="person">
      <h1 class="person__name">Odile Brevard</h1>
      <p class="person__role">Chef de Projet</p>
    </section>

    <ul class="contact">
      <li class="contact__item">
        <svg class="contact__icon" viewBox="0 0 16 16" aria-hidden="true"><path d="M4 1l2.5 3-1.5 2c1 2 3 4 5 5l2-1.5 3 2.5-2 2.5C7 14 2 9 1.5 3.5z" fill="var(--brand-red)"/></svg>
        +33 (0) 327 481 605
      </li>
      <li class="contact__item">
        <svg class="contact__icon" viewBox="0 0 16 16" aria-hidden="true"><rect x="4" y="1" width="8" height="14" rx="1.5" fill="none" stroke="var(--brand-red)" stroke-width="1.8"/><circle cx="8" cy="12.5" r="1" fill="var(--brand-red)"/></svg>
        06 42 19 37 64
      </li>
      <li class="contact__item">
        <svg class="contact__icon" viewBox="0 0 16 16" aria-hidden="true"><circle cx="8" cy="8" r="6.5" fill="none" stroke="var(--brand-red)" stroke-width="1.6"/><ellipse cx="8" cy="8" rx="2.8" ry="6.5" fill="none" stroke="var(--brand-red)" stroke-width="1.3"/><path d="M1.5 8h13" stroke="var(--brand-red)" stroke-width="1.3"/></svg>
        www.quorvexsystems.example
      </li>
      <li class="contact__item">
        <svg class="contact__icon" viewBox="0 0 16 16" aria-hidden="true"><rect x="1" y="3" width="14" height="10" rx="1" fill="none" stroke="var(--brand-red)" stroke-width="1.6"/><path d="M1.5 3.5L8 9l6.5-5.5" fill="none" stroke="var(--brand-red)" stroke-width="1.4"/></svg>
        o.brevard@o-vitalissystems.example
      </li>
    </ul>

    <address class="address">
      318 Rue Gaston Lemaire<br>
      59710 VALMERON
    </address>
  </article>
</body>
</html>
```